Sophisticated, clean website reflecting my feminine, playful side to sell my abstract art,

I need a website no more than 3 pages to showcase my paintings, a little about me and some contact info. I do abstracts so looking for something a little edgy, yet feminine and current.
Updates

Hi there, These are some artists websites that I Iike: Marnelvoss.com (I like how airy it is) peterwallombry.com garethpolvens.com (I like how it scrolls) I'll need a place for a photo ( a headshot-i do not have it yet so I'll need to be able to upload that later) as well as an area for my bio. Also, it's important that I will be able to upload any new photos and descriptions easily so it should be user friendly. Lastly, I like in a sunny place so would like to have this seem upbeat and playful as that is how i like to paint. thanks-I'm trying to upload my photos now -

Target Market(s)

ppl ages 35-70 who want large scale art for their homes

Industry/Entity Type

art

Coding

Coded - Design and coding required

Number of Pages Required

3 page

Colors

Designer to choose colors to be used in the design.

Requirements
Must have
• photos of my art, a place for my bio, be easy to reach me. tasteful-nothing too "in your face" -my clients are pretty high end and organized. They like clean lines
Nice to have
• sophisticated background, muted tones in the back-similar clean font throughout-no cursive
Should not have
• too many dark areas. Too many blocks of color. Too serious.

```html
<!DOCTYPE html>
<html lang="en">
<head>
<meta charset="utf-8">
<title>Clara Wendell — Abstract Art</title>
<link rel="stylesheet" href="https://fonts.googleapis.com/css2?family=Questrial&family=Playfair+Display&family=Mulish:wght@300;400&display=swap">
<style>
  :root {
    --ink: #161616;
    --text: #3a3a3a;
    --muted: #777777;
    --rule: #d6d6d6;
    --gold: #b9ad8a;
    --frame: #d3cdc3;
    --footer: #f5f5f5;
    --white: #ffffff;
    --arrow-bg: rgba(40, 40, 40, 0.55);
  }
  * { box-sizing: border-box; margin: 0; padding: 0; }
  html, body { width: 1200px; height: 2884px; overflow: hidden; }
  body { position: relative; background: var(--white); color: var(--text); font-family: "Mulish", sans-serif; }
  .abs { position: absolute; }

  /* header */
  .brand { top: 26px; left: 0; width: 1200px; display: flex; justify-content: center; align-items: center; gap: 16px; }
  .brand-mark { width: 44px; height: 44px; border: 3px solid var(--ink); }
  .brand-name { font-family: "Questrial", sans-serif; font-size: 44px; color: var(--ink); letter-spacing: 0.5px; line-height: 1; }
  .header-rule { top: 100px; left: 0; width: 1200px; height: 2px; background: var(--rule); }
  .nav { top: 121px; left: 0; width: 1200px; font-family: "Questrial", sans-serif; font-size: 16px; color: var(--text); }
  .nav a { position: absolute; color: inherit; text-decoration: none; white-space: nowrap; }
  .nav .active { color: var(--ink); }
  .nav .active::after { content: ""; position: absolute; left: 2px; right: 2px; top: 27px; height: 2px; background: var(--ink); }
  .social { display: flex; align-items: center; gap: 6px; }
  .social-dot { width: 32px; height: 32px; border-radius: 50%; background: var(--ink); display: inline-block; }

  /* hero */
  .hero { top: 170px; left: 0; width: 1200px; height: 640px;
    background: linear-gradient(120deg, #a9a59e 0%, #c9c4bb 12%, #c5661f 26%, #1f8a86 40%, #2f4f7a 50%, #c07a32 62%, #9c9990 78%, #d8cfa0 100%); }
  .hero-shade { top: 170px; left: 0; width: 1200px; height: 640px; background: linear-gradient(180deg, rgba(0,0,0,0) 55%, rgba(0,0,0,0.25) 100%); }
  .hero-arrow { width: 57px; height: 75px; background: var(--arrow-bg); display: flex; align-items: center; justify-content: center; }
  .hero-title { left: 0; width: 1200px; text-align: center; font-family: "Questrial", sans-serif; color: var(--white); line-height: 1; }
  .hero-title.small { top: 620px; font-size: 48px; }
  .hero-title.large { top: 680px; font-size: 70px; letter-spacing: 1px; }

  /* about */
  .about-frame { top: 891px; left: 17px; width: 477px; height: 335px; border-top: 3px solid var(--gold); border-right: 3px solid var(--gold); }
  .about-photo { top: 902px; left: 0; width: 482px; height: 474px; background: linear-gradient(180deg, #e1e3e5 0%, #d5d8db 60%, #c7cacd 100%); }
  .section-title { font-family: "Playfair Display", serif; color: var(--ink); font-weight: 400; line-height: 1; }
  .about-title { top: 956px; left: 565px; font-size: 54px; }
  .gold-bar { height: 3px; width: 64px; background: var(--gold); }
  .about-copy { top: 1047px; left: 566px; width: 584px; font-size: 17px; line-height: 27px; font-weight: 300; color: var(--text); }
  .about-copy p + p { margin-top: 14px; }

  /* gallery */
  .center { left: 0; width: 1200px; text-align: center; }
  .gallery-title { top: 1518px; font-size: 48px; }
  .gallery-frame { top: 1607px; left: 131px; width: 957px; height: 548px; border: 6px solid var(--frame); padding: 10px 12px; background: var(--white); }
  .gallery-art { width: 100%; height: 100%;
    background: linear-gradient(115deg, #3b3f66 0%, #8a6a9a 22%, #6a3f78 40%, #a07a8a 55%, #c9b9a6 70%, #7d5a8c 85%, #3d4570 100%); }

  /* contact */
  .contact-title { top: 2297px; font-size: 50px; }
  .contact-intro { top: 2378px; font-size: 19px; color: var(--text); }
  .contact-item { top: 2468px; display: flex; align-items: center; gap: 8px; font-family: "Questrial", sans-serif; color: var(--ink); white-space: nowrap; }

  /* footer */
  .footer { top: 2700px; left: 0; width: 1200px; height: 184px; background: var(--footer); }
  .footer-brand { top: 2741px; left: 127px; display: flex; align-items: center; gap: 8px; }
  .footer-mark { width: 44px; height: 44px; border: 3px solid var(--ink); }
  .footer-name { font-family: "Questrial", sans-serif; font-size: 30px; color: var(--ink); letter-spacing: 0.3px; }
  .footer-nav { top: 2752px; font-family: "Questrial", sans-serif; font-size: 17px; color: var(--ink); white-space: nowrap; }
  .copyright { top: 2829px; font-family: "Questrial", sans-serif; font-size: 14px; color: var(--text); }
</style>
</head>
<body>

<header>
  <div class="abs brand">
    <span class="brand-mark"></span>
    <span class="brand-name">CLARA WENDELL</span>
  </div>
  <div class="abs header-rule"></div>
  <nav class="abs nav">
    <a class="active" style="left:184px">HOME</a>
    <a style="left:344px">ABOUT ME</a>
    <a style="left:541px">GALLERY</a>
    <a style="left:727px">CONTACT</a>
    <a class="social" style="left:912px; top:-6px"><span class="social-dot"></span>@cwendellart</a>
  </nav>
</header>

<section>
  <div class="abs hero" role="img" aria-label="Close-up of an abstract painting with teal, orange and grey brush strokes"></div>
  <div class="abs hero-shade"></div>
  <div class="abs hero-arrow" style="top:413px; left:0">
    <svg width="22" height="34" viewBox="0 0 22 34"><path d="M17 3 L5 17 L17 31" fill="none" stroke="#fff" stroke-width="4"/></svg>
  </div>
  <div class="abs hero-arrow" style="top:413px; left:1143px">
    <svg width="22" height="34" viewBox="0 0 22 34"><path d="M5 3 L17 17 L5 31" fill="none" stroke="#fff" stroke-width="4"/></svg>
  </div>
  <div class="abs hero-title small">WELCOME TO</div>
  <div class="abs hero-title large">CLARA WENDELL</div>
</section>

<section>
  <div class="abs about-frame"></div>
  <div class="abs about-photo" role="img" aria-label="Portrait photo of the artist"></div>
  <h2 class="abs section-title about-title">ABOUT ME</h2>
  <div class="abs gold-bar" style="top:1024px; left:566px"></div>
  <div class="abs about-copy">
    <p>Lorem ipsum dolor sit amet, consectetur adipiscing elit, sed do eiusmod tempor incididunt ut labore et dolore magna aliqua. Ut enim ad minim veniam, quis nostrud exercitation</p>
    <p>Duis aute irure dolor in reprehenderit in voluptate velit esse cillum dolore eu fugiat nulla pariatur. Excepteur sint occaecat cupidatat non proident, sunt in culpa qui officia deserunt mollit anim id est laborum.Sed ut perspiciatis unde pariatur. Excepteur sint occaecat cupidatat non proident, sunt in culpa qui officia deserunt mollit anim id est laborum.Sed ut persmollit anim id est laborum.Sed ut perspiciatis unde pariatur. Excepteur sin</p>
  </div>
</section>

<section>
  <h2 class="abs section-title center gallery-title">PAINTING GALLERY</h2>
  <div class="abs gold-bar" style="top:1578px; left:562px"></div>
  <div class="abs gallery-frame">
    <div class="gallery-art" role="img" aria-label="Abstract painting in purple, violet, navy and cream tones"></div>
  </div>
  <svg class="abs" style="top:1850px; left:66px" width="26" height="44" viewBox="0 0 26 44"><path d="M22 3 L5 22 L22 41" fill="none" stroke="#8a8a8a" stroke-width="5"/></svg>
  <svg class="abs" style="top:1850px; left:1122px" width="26" height="44" viewBox="0 0 26 44"><path d="M4 3 L21 22 L4 41" fill="none" stroke="#8a8a8a" stroke-width="5"/></svg>
</section>

<section>
  <h2 class="abs section-title center contact-title">CONTACT US</h2>
  <div class="abs gold-bar" style="top:2353px; left:568px"></div>
  <p class="abs center contact-intro">Please get in touch with me on below details.</p>

  <div class="abs contact-item" style="left:177px; font-size:24px">
    <svg width="30" height="30" viewBox="0 0 30 30"><path d="M7 3 L11 3 L13 10 L10 12 Q13 19 18 21 L20 18 L27 20 L27 24 Q26 28 21 27 Q6 23 3 8 Q3 4 7 3 Z" fill="none" stroke="#222" stroke-width="1.5"/></svg>
    (555) 018 2746
  </div>
  <div class="abs contact-item" style="left:462px; font-size:24px">
    <svg width="32" height="24" viewBox="0 0 32 24"><rect x="1" y="1" width="30" height="22" fill="none" stroke="#222" stroke-width="1.5"/><path d="M1 1 L16 14 L31 1 M1 23 L12 11 M31 23 L20 11" fill="none" stroke="#222" stroke-width="1.5"/></svg>
    clarawendell@info.com
  </div>
  <div class="abs contact-item" style="left:817px; font-size:20px; color:#333">
    <svg width="34" height="34" viewBox="0 0 34 34"><circle cx="17" cy="17" r="15" fill="none" stroke="#222" stroke-width="1.5"/></svg>
    studiofeed @cwendellart
  </div>
</section>

<footer>
  <div class="abs footer"></div>
  <div class="abs footer-brand">
    <span class="footer-mark"></span>
    <span class="footer-name">CLARA WENDELL</span>
  </div>
  <div class="abs footer-nav" style="left:497px">ABOUT ME</div>
  <div class="abs footer-nav" style="left:649px">GALLERY</div>
  <div class="abs footer-nav" style="left:790px">CONTACT</div>
  <div class="abs footer-nav social" style="left:942px; top:2746px"><span class="social-dot"></span>@cwendellart</div>
  <p class="abs center copyright">© 2022 Clara Wendell &nbsp; All Rights Reserved</p>
</footer>

</body>
</html>
```